New Business Card Design Project

We require a business card design for Vexalund, a newly established Indian company.
Our focus is on the development, manufacturing, and export of a diverse array of pharmaceutical products on a global scale. The card should convey a professional appearance, as our primary markets are in Africa, China, and Southeast Asian nations.
We envision a two-sided business card, with the reverse side dedicated to a logo set against a solid color or an elegantly designed pattern. The corners should be rounded. We would appreciate seeing both horizontal and vertical design options. We trust the designer to utilize their expertise in creating this design.

The content for the business card is included in the attached Word file.

Target Market(s)

Our primary markets are in Africa, China, and Southeast Asian, Latin America, Maldives, Sri Lanka

Industry/Entity Type

Pharmaceutical Manufacturing and Export

Contact Information for Business Card

Colors

Designer to choose colors to be used in the design.

Requirements
Must have
• The reverse side of the business card features solely the logo along with the tagline, "Healing for Life."
Should not have
• The logo should not exceed two instances, encompassing both the front and back sides of the card.

```html
<!DOCTYPE html>
<html lang="en">
<head>
<meta charset="UTF-8">
<title>Vexalund Business Card</title>
<link rel="stylesheet" href="https://fonts.googleapis.com/css2?family=Lato:wght@400;700;900&display=swap">
<style>
  :root {
    --brand-blue: #29a9e0;
    --accent-red: #ef5a47;
    --ink: #1e1e1e;
    --paper: #ffffff;
    --backdrop: #3a3a3a;
  }
  * { box-sizing: border-box; margin: 0; padding: 0; }
  html, body {
    width: 1200px; height: 1200px; overflow: hidden;
    background: var(--backdrop);
    font-family: "Lato", sans-serif;
  }
  .canvas {
    width: 1200px; height: 1200px;
    display: flex; flex-direction: column;
    align-items: center; justify-content: center; gap: 50px;
  }
  .card {
    width: 900px; height: 515px;
    border-radius: 40px;
    position: relative;
    overflow: hidden;
  }
  /* Front side */
  .card-front {
    background: var(--paper);
    display: flex; align-items: center;
  }
  .front-brand {
    width: 430px;
    display: flex; align-items: center; justify-content: center; gap: 16px;
  }
  .brand-dot {
    width: 34px; height: 34px; border-radius: 50%;
    background: var(--accent-red);
    flex: none;
  }
  .brand-name {
    font-weight: 900; color: var(--brand-blue);
    font-size: 60px; letter-spacing: 0.5px; line-height: 1;
  }
  .divider {
    width: 2px; height: 250px; background: var(--brand-blue);
  }
  .front-details { padding-left: 50px; }
  .person-name {
    color: var(--brand-blue); font-weight: 400;
    font-size: 34px; letter-spacing: -0.5px; line-height: 1.1;
  }
  .person-role {
    color: var(--ink); font-size: 22px; margin-top: 6px;
    text-transform: uppercase; letter-spacing: 0.5px;
  }
  .contact-list { list-style: none; margin-top: 34px; }
  .contact-item {
    display: flex; align-items: flex-start; gap: 16px;
    font-size: 19px; color: var(--ink); line-height: 1.45;
  }
  .contact-item + .contact-item { margin-top: 2px; }
  .contact-item.address { margin-top: 18px; }
  .contact-icon { width: 18px; height: 18px; flex: none; margin-top: 5px; }
  /* Back side */
  .card-back {
    background: var(--brand-blue);
    display: flex; flex-direction: column;
    align-items: center; justify-content: center;
  }
  .back-brand { display: flex; align-items: center; gap: 26px; }
  .back-brand .brand-dot { width: 56px; height: 56px; background: var(--paper); }
  .back-brand .brand-name { color: var(--paper); font-size: 110px; }
  .tagline {
    color: var(--paper); font-weight: 700; font-size: 34px;
    margin-top: 34px; letter-spacing: 0.5px;
  }
</style>
</head>
<body>
<main class="canvas">
  <section class="card card-front" aria-label="Business card front">
    <div class="front-brand">
      <span class="brand-dot"></span>
      <span class="brand-name">Vexalund</span>
    </div>
    <div class="divider"></div>
    <div class="front-details">
      <h1 class="person-name">ARVIND KESSLER</h1>
      <p class="person-role">Managing Director</p>
      <ul class="contact-list">
        <li class="contact-item">
          <svg class="contact-icon" viewBox="0 0 24 24"><path fill="#ef5a47" d="M6.6 10.8a15 15 0 0 0 6.6 6.6l2.2-2.2c.3-.3.7-.4 1-.2 1.1.4 2.3.6 3.6.6.6 0 1 .4 1 1V20c0 .6-.4 1-1 1A17 17 0 0 1 3 4c0-.6.4-1 1-1h3.5c.6 0 1 .4 1 1 0 1.3.2 2.5.6 3.6.1.3 0 .7-.2 1z"/></svg>
          <span>044-987 210 654</span>
        </li>
        <li class="contact-item">
          <svg class="contact-icon" viewBox="0 0 24 24"><rect x="2" y="5" width="20" height="14" rx="1" fill="#ef5a47"/><path d="M3 6l9 7 9-7" stroke="#fff" stroke-width="2" fill="none"/></svg>
          <span>hello@vexalund.in</span>
        </li>
        <li class="contact-item">
          <svg class="contact-icon" viewBox="0 0 24 24"><circle cx="12" cy="12" r="10" fill="#ef5a47"/><path d="M2 12h20M12 2c3 3 3 17 0 20M12 2c-3 3-3 17 0 20" stroke="#fff" stroke-width="1.5" fill="none"/></svg>
          <span>www.vexalund.in</span>
        </li>
        <li class="contact-item address">
          <svg class="contact-icon" viewBox="0 0 24 24"><path fill="#ef5a47" d="M12 2a7 7 0 0 0-7 7c0 5 7 13 7 13s7-8 7-13a7 7 0 0 0-7-7zm0 9.5A2.5 2.5 0 1 1 12 6.5a2.5 2.5 0 0 1 0 5z"/></svg>
          <span>421, Address line goes here<br>45452, Country name</span>
        </li>
      </ul>
    </div>
  </section>

  <section class="card card-back" aria-label="Business card back">
    <div class="back-brand">
      <span class="brand-dot"></span>
      <span class="brand-name">Vexalund</span>
    </div>
    <p class="tagline">Healing for Life</p>
  </section>
</main>
</body>
</html>
```